Web Design Project - brivolta

I'm building an agency for marketing solutions but also medical education and patients education for pharmaceutical companies, medical societies and patient advocacy groups. We want to be perceived as the most innovative in the market. We work through design thinking solutions for campaigns and services.
I love some websites based on Swiss style design like www.quorlinex.com
We are a small group of designers, physicians and creatives working together to deliver the best experiences in our market.
We decided to also use pixel bazaar expecting that we maybe found a great idea we didn't thought about yet.

I'm extending it for more 2 weeks

Reason: I need the best design you can. Only PSD. No code needed. Love Swiss style, like velmora 5 and quorlinex.com I'm extending the deadline until get something great. Willing to extend as much as needed.

Target Market(s)

Pharmaceutical companies, physicians, medical societies, patients advocacy groups

Industry/Entity Type

Pharmaceutical

Font styles to use
Other font styles liked:
• Helvetia family

Colors

Designer to choose colors to be used in the design.

Requirements
Must have
• Must be innovative like www.quorlinex.com
Nice to have
• Cool menus
Should not have
• Not to appear too much Comercial. We like to be a boutique in this market. Craftsmen working with less clients at time but delivering precious stones.

```html
<!DOCTYPE html>
<html lang="en">
<head>
<meta charset="utf-8">
<title>Brivolta</title>
<link rel="stylesheet" href="https://fonts.googleapis.com/css2?family=Outfit:wght@200;300;400&display=swap">
<style>
:root{
  --page:#4a4a4b;
  --header:#3b3b3c;
  --card:#363637;
  --divider:#2f2f30;
  --accent:#e85555;
  --text:#ffffff;
  --muted:#c9c9c9;
  --footer:#343435;
  --sky:#3fbdf0;
  --blue:#4f78c9;
  --orange:#f5822f;
  --coral:#e4503f;
  --red:#e8403a;
  --amber:#f39b34;
}
*{box-sizing:border-box;margin:0;padding:0}
html,body{width:999px;height:1200px;overflow:hidden}
body{position:relative;background:var(--page);font-family:"Outfit",sans-serif;color:var(--text);font-weight:300}
.abs{position:absolute}

.site-header{left:0;top:0;width:999px;height:66px;background:var(--header);border-top:3px solid var(--accent)}
.menu-toggle{left:43px;top:18px;width:34px;height:30px}
.menu-toggle span{display:block;height:6px;background:#e6e6e6;margin-bottom:6px}
.header-rule{left:91px;top:0;width:3px;height:63px;background:var(--accent)}
.brand{left:111px;top:14px;font-size:28px;font-weight:300;letter-spacing:.3px}
.nav{left:262px;top:0;height:63px;display:flex}
.nav a{display:flex;align-items:center;justify-content:center;height:63px;border-left:1px solid var(--divider);border-right:1px solid #444}
.nav a:nth-child(1),.nav a:nth-child(2){width:56px}
.nav a:nth-child(3){width:64px}
.nav a:nth-child(4){width:60px}
.contacts-icon{left:928px;top:17px}

.card{background:var(--card)}
.card h2{font-weight:300;font-size:20px;line-height:1.2;text-align:center}
.card h2 b{font-weight:300;color:var(--accent)}
.card p{font-size:11.5px;line-height:1.45;text-align:center;color:var(--muted)}
.photo{display:block}

.marketing{left:43px;top:94px;width:223px;height:352px}
.marketing h2{margin-top:28px}
.marketing p{margin:20px 16px 0}
.marketing .photo{position:absolute;left:0;top:156px;width:223px;height:196px;background:linear-gradient(135deg,#cfd6d9,#9aa3a8 60%,#3f4448)}

.welcome{left:293px;top:94px;width:413px;height:352px;background:var(--accent);text-align:center;box-shadow:0 2px 4px rgba(0,0,0,.25)}
.welcome h1{font-weight:200;font-size:38px;margin-top:26px}
.welcome hr{border:0;border-top:1px solid rgba(255,255,255,.25);margin:18px 26px 0}
.welcome p{font-size:19px;line-height:1.65;margin:18px 22px 0;font-weight:300}
.dots{display:flex;justify-content:center;gap:3px;margin-top:24px}
.dots i{width:8px;height:8px;border-radius:50%;background:#2e2e2e}
.dots i.on{background:#fff}

.med-edu{left:734px;top:94px;width:222px;height:352px}
.med-edu .photo{width:222px;height:195px;background:linear-gradient(120deg,#e4eef3,#c8d8e2 50%,#eef3f5)}
.med-edu h2{margin-top:26px}
.med-edu p{margin:16px 14px 0}
.notch{width:0;height:0;border-left:7px solid transparent;border-right:7px solid transparent}

.patients{left:44px;top:477px;width:662px;height:222px;display:flex}
.patients .photo{width:388px;height:222px;background:linear-gradient(100deg,#5d6560,#d9dcd8 40%,#2e7d63 55%,#c9ccd0 75%,#38404a)}
.patients .body{flex:1;padding-top:38px}
.patients p{margin:18px 18px 0}

.advocacy{left:734px;top:473px;width:222px;height:547px;background:var(--accent)}
.advocacy .photo{width:222px;height:370px;background:radial-gradient(ellipse at 50% 40%,#c2bfc6,#7a767f 55%,#1e1c20)}
.advocacy h2{margin-top:20px}
.advocacy p{color:#fbe0e0;margin:18px 14px 0}

.societies{left:43px;top:724px;width:663px;height:296px;display:flex}
.societies .body{width:275px;padding-top:38px}
.societies p{margin:18px 8px 0 16px}
.societies p + p{margin-top:28px}
.societies .photo{width:388px;height:296px;background:linear-gradient(110deg,#d7dde2,#b6c2cb 45%,#f2f2f2 70%,#8a98a8)}

.social{top:1046px;width:93px;height:64px;padding:14px 0 0 7px;font-size:8.5px;color:#fff}
.social .count{display:block;margin-bottom:12px}
.social .mark{position:absolute;right:10px;bottom:12px;width:22px;height:22px;border-radius:50%;background:rgba(255,255,255,.9)}

.site-footer{left:0;top:1138px;width:999px;height:62px;background:var(--footer);font-size:10px;text-align:center;line-height:62px;color:#e0e0e0}
</style>
</head>
<body>

<header class="site-header abs">
  <div class="menu-toggle abs"><span></span><span></span><span></span></div>
  <div class="header-rule abs"></div>
  <div class="brand abs">Brivolta</div>
  <nav class="nav abs">
    <a href="#" aria-label="Home"><svg width="18" height="16" viewBox="0 0 18 16"><path d="M9 1 1 8h2v7h4v-5h4v5h4V8h2z" fill="#e85555"/></svg></a>
    <a href="#" aria-label="Team"><svg width="20" height="16" viewBox="0 0 20 16" fill="#fff"><circle cx="6" cy="5" r="3"/><circle cx="14" cy="5" r="3"/><path d="M0 15c0-4 3-6 6-6s6 2 6 6zM9 15c0-4 2-6 5-6s6 2 6 6z"/></svg></a>
    <a href="#" aria-label="Settings"><svg width="18" height="18" viewBox="0 0 18 18"><circle cx="9" cy="9" r="6" fill="none" stroke="#fff" stroke-width="4" stroke-dasharray="3 1.7"/><circle cx="9" cy="9" r="4.5" fill="#fff"/><circle cx="9" cy="9" r="2" fill="#3b3b3c"/></svg></a>
    <a href="#" aria-label="Call"><svg width="18" height="18" viewBox="0 0 18 18"><path d="M4 1l3 4-2 2c1 3 3 5 6 6l2-2 4 3-2 3C8 17 1 10 1 3z" fill="#fff"/></svg></a>
  </nav>
  <svg class="contacts-icon abs" width="28" height="28" viewBox="0 0 28 28" aria-label="Contacts"><rect x="1" y="1" width="24" height="26" fill="#fff"/><rect x="5" y="4" width="17" height="20" fill="#3b3b3c"/><circle cx="15" cy="10" r="3" fill="#fff"/><path d="M9 20c0-4 3-5 6-5s6 1 6 5z" fill="#fff"/><rect x="24" y="5" width="4" height="4" fill="#fff"/><rect x="24" y="12" width="4" height="4" fill="#fff"/><rect x="24" y="19" width="4" height="4" fill="#fff"/></svg>
</header>

<section class="card marketing abs">
  <h2>M<b>a</b>rketing Solutions</h2>
  <p>Sed ut perspiciatis unde omnis iste natus error sit voluptatem accusantium doloremque laudantium</p>
  <div class="photo" role="img" aria-label="Team working over a table of design sketches and colour swatches"></div>
</section>

<section class="welcome abs">
  <h1>Welcome to Brivolta</h1>
  <hr>
  <p>Sed ut perspiciatis unloede omnis iste natus error sit voluptatem accusantium doloremque laudantium, totam rem aperiam, eaque ipsa quloreae ab illo ivetore veritatis et quasi architbeatae. vitae dicta sunt explicabo.</p>
  <div class="dots"><i></i><i></i><i></i><i class="on"></i><i></i></div>
</section>

<section class="card med-edu abs">
  <div class="photo" role="img" aria-label="Young doctors in white coats with stethoscopes"></div>
  <div class="notch abs" style="left:104px;top:188px;border-bottom:7px solid var(--card)"></div>
  <h2>Medical Educ<b>a</b>tion</h2>
  <p>Sed ut perspiciatis unde omnis iste natus error sit voluptatem accusantium doloremque laudantium</p>
</section>

<section class="card patients abs">
  <div class="photo" role="img" aria-label="Medical staff meeting in a bright hospital hall"></div>
  <div class="body">
    <h2>P<b>a</b>tients Education for<br>Pharmaceutical Companies</h2>
    <p>Sed ut perspiciatis unde omnis iste natus error sit voluptatem accusantium doloremque laudant illo inventore veritatis et quasi</p>
  </div>
</section>

<section class="card advocacy abs">
  <div class="photo" role="img" aria-label="Cupped hands holding a paper cut-out of a family"></div>
  <div class="notch abs" style="left:104px;top:363px;border-bottom:7px solid var(--accent)"></div>
  <h2>P<b style="color:#3a3a3a">a</b>tient Advocacy<br>Groups</h2>
  <p>Sed ut perspiciatis unde omnis iste natus error sit voluptatem accusantium doloremque laudantium</p>
</section>

<section class="card societies abs">
  <div class="body">
    <h2>Medic<b>a</b>l Societies</h2>
    <p>Sed ut perspiciatis unde omnis iste natus error sit voluptatem accusantium doloremque laudantium, totam rem aperiam, eaque</p>
    <p>Sed ut perspiciatis unde omnis iste natus error sit voluptatem accusantium doloremque laudantium, totam rem aperiam, eaque ipsa quae ab. illo inventore veritatis et.</p>
  </div>
  <div class="photo" role="img" aria-label="Senior doctor reading a tablet in a laboratory"></div>
  <div class="notch abs" style="left:275px;top:140px;border:7px solid transparent;border-left-color:var(--card);border-right:0"></div>
</section>

<a class="social abs" style="left:173px;background:var(--sky)"><span class="count">20000</span>Followers<i class="mark"></i></a>
<a class="social abs" style="left:285px;background:var(--blue)"><span class="count">20000</span>People like it<i class="mark"></i></a>
<a class="social abs" style="left:396px;background:var(--orange)"><span class="count">20000</span>Listeners<i class="mark"></i></a>
<a class="social abs" style="left:508px;background:var(--coral)"><span class="count">20000</span>In Circles<i class="mark"></i></a>
<a class="social abs" style="left:619px;background:var(--red)"><span class="count">20000</span>Subscribers<i class="mark"></i></a>
<a class="social abs" style="left:731px;background:var(--amber)"><span class="count">20000</span>Subscribers<i class="mark"></i></a>

<footer class="site-footer abs">©2014 Brivolta all copyrights are reserved</footer>

</body>
</html>
```